Flowmark Engineering Business Card

our company has just rebranded and taken on a new logo design. We now need to update our business cards with the new logo. This is also an opportunity to reformat and modernize our look. We are an engineering company so the look needs to be formal and professional yet it should look modern. Have a look at our current card and the new card should have the same information.

Target Market(s)

Engineering firms, government, mining companies

Industry/Entity Type

Mechanical Engineering

Contact Information for Business Card

see example attached

Requirements
Must have
• look professional and modern
Should not have
• should not include the office locations 'Brisbane, Sydney and Kuala Lumpur'
• you will find this on the example but it should not be included in these versions. please remove from your submissions and resubmit

```html
<!DOCTYPE html>
<html lang="en">
<head>
<meta charset="utf-8">
<title>Flowmark Engineering Business Card</title>
<link href="https://fonts.googleapis.com/css2?family=Exo+2:wght@400;600;700&display=swap" rel="stylesheet">
<style>
  :root {
    --backdrop: #e6e7ea;
    --card: #ffffff;
    --brand-blue: #2e3d9c;
    --sky-blue: #1f8fe0;
    --deep-blue: #2b52c4;
    --band-grey: #7d7f83;
    --text-dark: #33353a;
    --text-soft: #5a5d63;
  }
  * { margin: 0; padding: 0; box-sizing: border-box; }
  html, body { width: 1200px; height: 901px; overflow: hidden; }
  body {
    background: var(--backdrop);
    font-family: "Exo 2", sans-serif;
    position: relative;
  }
  .card {
    position: absolute;
    top: 300px;
    width: 520px;
    height: 300px;
    background: var(--card);
    border-radius: 26px;
    overflow: hidden;
    box-shadow: 0 6px 18px rgba(0,0,0,0.12);
  }
  .card--front { left: 60px; }
  .card--back { left: 620px; }

  .front-swoosh { position: absolute; left: 0; top: 0; width: 520px; height: 300px; }

  .brand {
    position: absolute;
    display: flex;
    align-items: center;
    gap: 12px;
    color: var(--brand-blue);
  }
  .brand__dot {
    width: 34px; height: 34px;
    border-radius: 50%;
    background: var(--brand-blue);
    flex: none;
  }
  .brand__name {
    font-weight: 700;
    font-size: 30px;
    line-height: 1;
    letter-spacing: 1px;
    text-transform: uppercase;
  }
  .brand__name span { display: block; font-size: 15px; letter-spacing: 7px; margin-top: 4px; }

  .card--front .brand { left: 200px; top: 48px; }
  .card--back .brand { left: 50%; top: 50%; transform: translate(-50%, -50%); }

  .person { position: absolute; left: 168px; top: 136px; }
  .person__name {
    font-size: 15px; font-weight: 600; letter-spacing: 1.5px;
    color: var(--brand-blue); text-transform: uppercase;
  }
  .person__role { font-size: 11px; color: var(--text-soft); margin-top: 2px; }

  .contact {
    position: absolute; right: 30px; top: 140px;
    list-style: none; text-align: right;
    font-size: 11px; color: var(--text-dark); line-height: 20px;
  }
  .contact li { display: flex; justify-content: flex-end; align-items: center; gap: 8px; }
  .contact .address { display: block; margin-bottom: 4px; line-height: 15px; }
  .contact svg { width: 11px; height: 11px; fill: var(--brand-blue); flex: none; }
</style>
</head>
<body>
  <section class="card card--front" aria-label="Business card front">
    <svg class="front-swoosh" viewBox="0 0 520 300" aria-hidden="true">
      <defs>
        <linearGradient id="blueBand" x1="0" y1="0" x2="1" y2="1">
          <stop offset="0" stop-color="var(--sky-blue)"/>
          <stop offset="1" stop-color="var(--deep-blue)"/>
        </linearGradient>
      </defs>
      <path d="M0 0 H120 C80 90 110 210 190 300 H0 Z" fill="var(--band-grey)"/>
      <path d="M0 0 H90 C50 90 70 200 130 300 H0 Z" fill="#ffffff"/>
      <path d="M0 0 H78 C40 90 58 200 112 300 H0 Z" fill="url(#blueBand)"/>
    </svg>

    <div class="brand">
      <span class="brand__dot"></span>
      <p class="brand__name">Flowmark<span>Engineering</span></p>
    </div>

    <div class="person">
      <p class="person__name">Daniel Hart</p>
      <p class="person__role">Managing Director</p>
    </div>

    <ul class="contact">
      <li class="address">12, 4th Floor Harbour<br>Court Road</li>
      <li>012 555 0142
        <svg viewBox="0 0 24 24"><path d="M6.6 10.8a15 15 0 0 0 6.6 6.6l2.2-2.2a1 1 0 0 1 1-.25 11.4 11.4 0 0 0 3.6.57 1 1 0 0 1 1 1V20a1 1 0 0 1-1 1A17 17 0 0 1 3 4a1 1 0 0 1 1-1h3.5a1 1 0 0 1 1 1c0 1.25.2 2.45.57 3.57a1 1 0 0 1-.25 1z"/></svg>
      </li>
      <li>012 555 0187
        <svg viewBox="0 0 24 24"><path d="M7 1h10a2 2 0 0 1 2 2v18a2 2 0 0 1-2 2H7a2 2 0 0 1-2-2V3a2 2 0 0 1 2-2zm0 3v15h10V4z"/></svg>
      </li>
      <li>d.hart@flowmark.example
        <svg viewBox="0 0 24 24"><path d="M2 5h20v14H2zm2 2v.4l8 5 8-5V7z"/></svg>
      </li>
      <li>www.flowmarkeng.example
        <svg viewBox="0 0 24 24"><path d="M12 2a10 10 0 1 0 0 20 10 10 0 0 0 0-20zm0 2c.9 0 2.2 2.2 2.6 7H9.4C9.8 6.2 11.1 4 12 4zm-3 .6A14 14 0 0 0 7.4 11H4.1A8 8 0 0 1 9 4.6zm6 0a8 8 0 0 1 4.9 6.4h-3.3A14 14 0 0 0 15 4.6zM4.1 13h3.3A14 14 0 0 0 9 19.4 8 8 0 0 1 4.1 13zm5.3 0h5.2c-.4 4.8-1.7 7-2.6 7s-2.2-2.2-2.6-7zm7.2 0h3.3a8 8 0 0 1-4.9 6.4 14 14 0 0 0 1.6-6.4z"/></svg>
      </li>
    </ul>
  </section>

  <section class="card card--back" aria-label="Business card back">
    <div class="brand">
      <span class="brand__dot"></span>
      <p class="brand__name">Flowmark<span>Engineering</span></p>
    </div>
  </section>
</body>
</html>
```